Chateau de Vermirelle multiple flyers

PRICE OFFERED IS PER FLYER IE: €139 PER FLYER OR €695 TOTAL WITH OTHERS TO FOLLOW

I want to creat a common design across a range of flyers that I will be handing out to visitors to our Christmas market, but will also be used throughout the year and years to come. The final design will need to be adapted so the copy can be translated into french as well as English. So I would need an ai or paint version as well as pdf's etc.

There are 5 flyers to be designed at this stage the PRICE OFFERED IS PER FLYER IE: €139 PER FLYER OR €695 TOTAL WITH OTHERS TO FOLLOW

1. Seminars at the chateau - 4 page 1/3 A4 double sided (No longer referring to full chateau rental)
2. Accomodation at the chateau 2 page 1/3 A4 double sided (Seasons simplified now: Peak = July & August and Christmas week; High, June and September. Low: Rest of year.)
3. QBVA 2 Award in Wine and Spirits 4 page 1/3 A4 double sided
See current offering at
http://www.valcharmille.example/experiences-and-tours/wine-tours/qbva-level-2-loire-valley-derek-pallister/#1467282665644-f1124b7e-5513

With photos here:
https://www.filecrate.example/sh/qpt482nzkdbvxar/AAAX3mRTyLpoW-Bnuk7hjdzke?dl=0

4. Valentine's/Romantic package 2 page 1/3 A4 double sided
5. Mothers Day package 2 page 1/3 A4 double sided.

The first two are very urgent as need to be available by Wednesday 7th December to go to print.

In the future we will be looking to add to the range with:

6. Wedding Brochure - 6 page 1/3 A4 double sided
7. Group celebrations - 6 page 1/3 A4 double sided
8. Pamper/Wellness package - 2 page 1/3 A4 double sided
9. Activity Break - 2 page 1/3 A4 double sided.

I have attached some examples of what we have to date, which are not consistent. As well as some excel spreadhseets which explain the packages. Along with an architects plan of the ground floor (may help with the seminar brochure.)

I have also provided a link to our gallery of photos that can be used and a couple of videos to give you a feel for the place.

https://www.filecrate.example/sh/k7vbnrzq2pwdoyt/AACJXNsPuelk8BHdrt2VhLmYe?dl=0

Target Market(s)

Adults aged 34 plus.
Seminars = Local businesses
Accommodation = 34 plus high income
Wedding = Females 28 plus high income

Requirements
Must have
• Demonstrates 5 star luxury and quality.

```html
<!DOCTYPE html>
<html lang="en">
<head>
<meta charset="utf-8">
<title>Seminars at the Chateau – Brochure Spread</title>
<link href="https://fonts.googleapis.com/css2?family=Crimson+Text:wght@400;600&family=Lato:wght@400;700&family=Yellowtail&display=swap" rel="stylesheet">
<style>
  :root {
    --backdrop: #d6dfae;
    --paper: #ffffff;
    --gold: #c4a565;
    --ink: #3a3a3a;
    --ink-soft: #6b6b6b;
    --teal: #2aa6b5;
    --badge-blue: #2f5fa8;
    --spine: #e4e4e4;
  }
  * { box-sizing: border-box; margin: 0; padding: 0; }
  html, body {
    width: 1200px; height: 701px; overflow: hidden;
    background: var(--backdrop);
  }
  .spread {
    position: absolute; left: 260px; top: 110px;
    width: 680px; height: 480px;
    display: flex;
  }
  .page {
    position: relative; width: 340px; height: 480px;
    background: var(--paper); overflow: hidden;
  }
  .page--left { border-right: 1px solid var(--spine); }
  .photo { position: absolute; }

  /* left page */
  .gold-band {
    position: absolute; left: 0; top: 128px; width: 150px; height: 284px;
    background: var(--gold);
  }
  .collage {
    position: absolute; left: 47px; top: 29px; width: 225px; height: 150px;
    display: grid; grid-template-columns: 1fr 1fr; grid-template-rows: 1fr 1fr; gap: 2px;
    background: var(--paper);
  }
  .collage .tile--chateau { background: linear-gradient(160deg, #4a6fa8, #c9b7a0 60%, #5c4a3a); }
  .collage .tile--cellar  { background: linear-gradient(160deg, #5a3418, #b07a3e 55%, #3a200f); }
  .collage .tile--terrace { background: linear-gradient(160deg, #8a2a22, #e7c7a0 55%, #6b4a38); }
  .collage .tile--oven    { background: radial-gradient(circle at 50% 60%, #f3a24a, #b6452a 55%, #3d1d16); }
  .photo--grapes {
    left: 47px; top: 214px; width: 225px; height: 151px;
    background: radial-gradient(ellipse at 50% 55%, #2d2f4a 0%, #4b5470 35%, #c9ced8 75%, #e3e6ea 100%);
  }
  .caption { position: absolute; font-family: "Lato", sans-serif; font-size: 5px; line-height: 1.5; }
  .caption__title { display: block; font-size: 5.5px; }
  .caption--collage { left: 141px; top: 186px; width: 131px; text-align: right; color: var(--ink); }
  .caption--collage .caption__title { color: var(--teal); }
  .caption--grapes { left: 55px; top: 372px; width: 90px; color: #fff; }
  .cert-badge {
    position: absolute; left: 188px; top: 376px; width: 74px; height: 47px;
    border: 2px solid var(--badge-blue); border-radius: 4px;
  }

  .folio {
    position: absolute; top: 461px; font-family: "Lato", sans-serif;
    font-size: 5px; color: var(--ink-soft); letter-spacing: 0.3px;
  }
  .folio--left { left: 30px; }
  .folio--right { right: 30px; }
  .folio span { margin: 0 6px; }

  /* right page */
  .photo--estate {
    left: 0; top: 29px; width: 311px; height: 220px;
    background: linear-gradient(180deg, #7fb2e6 0%, #cfe1f2 45%, #b9a47a 62%, #8a7a4a 100%);
  }
  .photo--vines {
    left: 200px; top: 29px; width: 111px; height: 220px;
    background: linear-gradient(180deg, #3f6a2a, #5b8a34 50%, #3b2f4a 80%, #6e6235);
  }
  .estate-name {
    position: absolute; left: 143px; top: 196px; width: 162px; height: 51px;
    background: rgba(255,255,255,0.82);
    display: flex; align-items: center; justify-content: center; gap: 6px;
    font-family: "Crimson Text", serif; font-size: 8px; letter-spacing: 1.5px;
    text-transform: uppercase; color: var(--ink);
  }
  .estate-name__mark { width: 7px; height: 7px; background: var(--ink); }
  .headline {
    position: absolute; left: 46px; top: 262px; width: 110px;
    font-family: "Yellowtail", cursive; font-weight: 400;
    font-size: 27px; line-height: 0.95; color: #2a2a2a;
  }
  .intro {
    position: absolute; left: 163px; top: 279px; width: 152px;
    font-family: "Crimson Text", serif; font-size: 5.2px; line-height: 1.45; color: var(--ink);
  }
  .intro p + p, .body-copy p + p { margin-top: 5px; }
  .body-copy {
    position: absolute; left: 51px; top: 371px; width: 264px;
    font-family: "Crimson Text", serif; font-size: 5.2px; line-height: 1.45; color: var(--ink);
  }
</style>
</head>
<body>
  <main class="spread">
    <section class="page page--left">
      <div class="gold-band"></div>
      <div class="collage">
        <div class="tile tile--chateau" role="img" aria-label="Chateau exterior with stone steps"></div>
        <div class="tile tile--cellar" role="img" aria-label="Wine cellar with barrels"></div>
        <div class="tile tile--terrace" role="img" aria-label="Red canopied terrace"></div>
        <div class="tile tile--oven" role="img" aria-label="Bread baking in a wood-fired oven"></div>
      </div>
      <p class="caption caption--collage">
        <span class="caption__title">Description goes here</span>
        Vaulted cellars and candlelit dinners await every guest after a long day.
      </p>
      <div class="photo photo--grapes" role="img" aria-label="Hands holding a bunch of dark grapes"></div>
      <p class="caption caption--grapes">
        <span class="caption__title">Description goes here</span>
        Hand-picked grapes from our own vines.
      </p>
      <div class="cert-badge" role="img" aria-label="Wine and spirits certification badge"></div>
      <footer class="folio folio--left">24<span>Chateau</span></footer>
    </section>

    <section class="page page--right">
      <div class="photo photo--estate" role="img" aria-label="Chateau towers beside a river under blue sky"></div>
      <div class="photo photo--vines" role="img" aria-label="Vine leaves with ripe grape clusters"></div>
      <div class="estate-name"><span class="estate-name__mark"></span>Chateau de Vermirelle</div>

      <h1 class="headline">Seminars<br>at the<br>Chateau</h1>

      <div class="intro">
        <p>Bright meeting rooms overlook the park and the river valley beyond.</p>
        <p>Every day includes coffee breaks, lunch and full audio-visual support.</p>
        <p>Teams can unwind with a guided cellar tour and a tasting of local wines. Evening dinners are served in the grand dining hall by candlelight.</p>
      </div>

      <div class="body-copy">
        <p>Our seminar packages bring your team together in a calm setting far from the office. Each room offers natural light, fast wifi and a flexible layout for workshops, talks or quiet planning sessions.</p>
        <p>Stay overnight in elegant rooms, start the morning with a walk through the vineyard and return to work refreshed. Ask us about tailored menus and group activities.</p>
      </div>

      <footer class="folio folio--right"><span>Seminars</span>25</footer>
    </section>
  </main>
</body>
</html>
```